Business Card Design For Marketing Agnecy LVP

Need business card design for marketing agency.

Doug Fenwick
President, CEO
1-555-302-4196
doug@boldpromoperksgroup.example
www.BoldPromoPerksGroup.example

Back Side:
Boost Sales Using Rewards, Incentives & Giveaways
Get A Free Sample Package

Target Market(s)

B2B

Industry/Entity Type

Marketing

Contact Information for Business Card

Doug Fenwick
President, CEO
1-555-302-4196

Back Side:
Get A Free Sample Package

Please note that my current url is OLD DESIGN. I am working on new design and want the business card to match color themes at least on new site. Here is the demo link for new site so you can see the colors I use, etc.

http://layoutcratehub.example/kq/doug/lvp_final/index.html

Requirements
Must have
• Please note that my current url is OLD DESIGN. I am working on new design and want the business card to match color themes at least on new site. Here is the demo link for new site so you can see the colors I use, etc.

Nice to have

Should not have

```html
<!DOCTYPE html>
<html lang="en">
<head>
<meta charset="utf-8">
<title>LVP Business Card</title>
<link rel="stylesheet" href="https://fonts.googleapis.com/css2?family=Montserrat:wght@500;700;800&family=Roboto:wght@400;500&display=swap">
<style>
  :root {
    --bg: #c9c9c9;
    --card: #f3f3f3;
    --blue: #2a5592;
    --dark: #3b3b3d;
    --green: #4cae3b;
    --text: #2e2e2e;
    --white: #ffffff;
  }
  * { margin: 0; padding: 0; box-sizing: border-box; }
  html, body { width: 1200px; height: 576px; overflow: hidden; }
  body { background: var(--bg); position: relative; font-family: "Roboto", sans-serif; color: var(--text); }

  .card {
    position: absolute; top: 138px; width: 484px; height: 294px;
    background: var(--card); border-radius: 10px; overflow: hidden;
  }
  .card--back { left: 82px; }
  .card--front { left: 602px; }

  .brand { position: absolute; display: flex; align-items: center; gap: 14px; }
  .brand__dot { width: 22px; height: 22px; border-radius: 50%; background: var(--blue); flex: none; }
  .brand__name {
    font-family: "Montserrat", sans-serif; font-weight: 700; color: var(--blue);
    font-size: 30px; line-height: 1.05; letter-spacing: 0.5px;
  }
  .brand__name small { display: block; font-size: 15px; letter-spacing: 2.5px; font-weight: 700; }
  .card--back .brand { left: 56px; top: 40px; }
  .card--front .brand { left: 40px; top: 40px; }

  .offer { position: absolute; left: 62px; top: 146px; width: 360px; height: 68px; }
  .offer svg { position: absolute; inset: 0; }
  .offer__line { position: absolute; left: 0; right: 0; text-align: center; color: var(--white); }
  .offer__tagline { top: 7px; font-size: 12.5px; }
  .offer__cta { top: 25px; font-family: "Montserrat", sans-serif; font-weight: 800; font-size: 13px; letter-spacing: 0.6px; }

  .web-link { position: absolute; top: 248px; left: 0; right: 0; text-align: center; font-size: 13px; }
  .web-link span { color: var(--blue); }

  .edge-strip { position: absolute; left: 0; right: 0; bottom: 0; height: 12px; display: flex; }
  .edge-strip__blue { flex: 1; background: var(--blue); }
  .edge-strip__dark { flex: 1; background: var(--dark); }

  .contact { position: absolute; left: 40px; top: 142px; list-style: none; font-size: 12px; }
  .contact li { display: flex; align-items: center; gap: 8px; height: 18px; }
  .contact svg { width: 10px; height: 10px; fill: var(--blue); }

  .waves { position: absolute; inset: 0; }
  .person { position: absolute; right: 24px; top: 228px; text-align: right; color: var(--white); }
  .person__name { font-family: "Montserrat", sans-serif; font-weight: 700; font-size: 19px; }
  .person__role { font-size: 12px; margin-top: 4px; }
</style>
</head>
<body>

<section class="card card--back">
  <div class="brand">
    <span class="brand__dot"></span>
    <div class="brand__name">LVP BOLD PROMO<small>PERKS GROUP</small></div>
  </div>

  <div class="offer">
    <svg viewBox="0 0 360 68" preserveAspectRatio="none">
      <path d="M3 0 H357 L350 44 L180 50 L10 44 Z" fill="var(--green)"/>
      <path d="M8 49 L180 55 L352 49 L352 53 L180 64 L8 53 Z" fill="var(--dark)"/>
    </svg>
    <p class="offer__line offer__tagline">Boost Sales Using Rewards, Incentives &amp; Giveaways</p>
    <p class="offer__line offer__cta">GET A FREE SAMPLE PACKAGE</p>
  </div>

  <p class="web-link">www.<span>BoldPromoPerksGroup</span>.example</p>

  <div class="edge-strip"><span class="edge-strip__blue"></span><span class="edge-strip__dark"></span></div>
</section>

<section class="card card--front">
  <div class="brand">
    <span class="brand__dot"></span>
    <div class="brand__name">LVP BOLD PROMO<small>PERKS GROUP</small></div>
  </div>

  <ul class="contact">
    <li><svg viewBox="0 0 10 10"><path d="M1 3 Q5 0 9 3 L8 4.5 L6.5 3.8 V3 H3.5 V3.8 L2 4.5 Z M2 5 H8 L9 9 H1 Z"/></svg>1-555-302-4196</li>
    <li><svg viewBox="0 0 10 10"><path d="M0 2 H10 V8 H0 Z" /><path d="M0.5 2.5 L5 5.5 L9.5 2.5" stroke="var(--card)" stroke-width="1" fill="none"/></svg>doug@boldpromoperksgroup.example</li>
    <li><svg viewBox="0 0 10 10"><circle cx="5" cy="5" r="4.5"/><path d="M0.5 5 H9.5 M5 0.5 V9.5" stroke="var(--card)" stroke-width="0.8"/></svg>www.BoldPromoPerksGroup.example</li>
  </ul>

  <svg class="waves" viewBox="0 0 484 294" preserveAspectRatio="none">
    <path d="M0 250 C70 300 190 300 290 250 S430 170 484 190 V294 H0 Z" fill="var(--blue)"/>
    <path d="M0 228 C90 290 200 290 300 232 S440 160 484 182" stroke="var(--dark)" stroke-width="7" fill="none"/>
    <path d="M0 236 C60 270 140 280 240 262" stroke="var(--dark)" stroke-width="4" fill="none"/>
  </svg>

  <div class="person">
    <p class="person__name">Doug Fenwick</p>
    <p class="person__role">President, CEO</p>
  </div>
</section>

</body>
</html>
```